Bright Path Academy - Personal Development business 2.0 needs a social post format design.

https://www.brightpathacademy.example

Our focus with Bright Path Academy is on developing people through knowledge and skills to improve their everyday lives.
We love simplicity, Quince design and less is more.

We are crazy about personal growth, science, design, the latest gadgets and people.

We need 4 formats for our social media posts.
1. Blogs -to pronounce a blog post
2. Workshop /training - to pronounce our workshops/trainings (both online and offline)
3. Podcast - called "Kijk eens verder". To pronounce a guest we've spoken. The host is called Berend.
4. Facts - to pronounce short facts about personal development. Invites people to read more.
The formats should include: high quality pictogram (better than the uploaded picto's), 1 of the 3 logo's in the design.
It's important that we can edit the design in Affinity Design / Affinity Photo to adjust the text in the format.

Attached you find four of our current designs, which are a poor example of how the designs should look like. These are just to show you how much lines of text (more or less) will be in the designs. So please do not make a design that looks like these ;) You have carte blanche.

Our customers are mostly women (80%). We focus on both business and casual customers.

Target Market(s)

80% woman, 20% men. We focus on both business and casual customers.

Requirements
Must have
• Less is more. Quince Design alike. Simplicity.
Aimed at the women target audience.
Designs must be edible for adjusting the text in the format.
Nice to have
• Unique concept.
The design should "breathe".
Each design can have a different color, so customers identify the specific post with specific information. For example, blog is red, workshop post black, etc.

```html
<!DOCTYPE html>
<html lang="nl">
<head>
<meta charset="utf-8">
<title>Bright Path Academy – social post formats</title>
<link href="https://fonts.googleapis.com/css2?family=DM+Sans:wght@400;500;700&display=swap" rel="stylesheet">
<style>
  :root {
    --canvas: #ebebeb;
    --white: #ffffff;
    --training-bg: #f2f1ef;
    --training-accent: #1c1c1c;
    --training-photo-a: #8a8a8a;
    --training-photo-b: #3a3a3a;
    --blog-bg: #fcefdf;
    --blog-accent: #d9701c;
    --blog-photo-a: #f7c878;
    --blog-photo-b: #c98a2e;
    --facts-bg: #e6f1e9;
    --facts-accent: #136b3c;
    --facts-photo-a: #bfe0c9;
    --facts-photo-b: #2f7a4a;
    --podcast-bg: #e4edf6;
    --podcast-accent: #0d5fa3;
    --podcast-photo-a: #a9c7e6;
    --podcast-photo-b: #24578c;
  }
  * { box-sizing: border-box; margin: 0; padding: 0; }
  html, body {
    width: 1200px; height: 600px; overflow: hidden;
    background: var(--canvas);
    font-family: "DM Sans", Arial, sans-serif;
  }
  .post {
    position: absolute; top: 166px;
    width: 270px; height: 270px; overflow: hidden;
    border-radius: 6px;
    background: var(--bg);
    color: var(--accent);
  }
  .post--training { left: 21px;  --bg: var(--training-bg); --accent: var(--training-accent); --photo-a: var(--training-photo-a); --photo-b: var(--training-photo-b); }
  .post--blog     { left: 317px; --bg: var(--blog-bg);     --accent: var(--blog-accent);     --photo-a: var(--blog-photo-a);     --photo-b: var(--blog-photo-b); }
  .post--facts    { left: 613px; --bg: var(--facts-bg);    --accent: var(--facts-accent);    --photo-a: var(--facts-photo-a);    --photo-b: var(--facts-photo-b); }
  .post--podcast  { left: 909px; --bg: var(--podcast-bg);  --accent: var(--podcast-accent);  --photo-a: var(--podcast-photo-a);  --photo-b: var(--podcast-photo-b); }

  .post__photo {
    position: absolute; left: 164px; top: 20px;
    width: 86px; height: 150px;
    border-radius: 43px 43px 6px 6px;
    background: linear-gradient(160deg, var(--photo-a), var(--photo-b));
  }

  .brand {
    position: absolute; left: 20px; top: 22px;
    display: flex; align-items: center; gap: 5px;
    font-size: 9px; font-weight: 500; letter-spacing: 0.3px;
    white-space: nowrap;
  }
  .brand__dot { width: 6px; height: 6px; border-radius: 50%; background: var(--accent); }

  .content { position: absolute; left: 20px; top: 52px; width: 136px; }
  .kicker { font-size: 11px; font-weight: 400; line-height: 1.25; margin-bottom: 6px; }
  .headline { font-size: 17px; font-weight: 700; line-height: 1.12; letter-spacing: -0.2px; }
  .headline--caps { font-size: 19px; line-height: 1.08; }
  .detail { margin-top: 8px; font-size: 11px; font-weight: 400; line-height: 1.3; }

  .rule {
    position: absolute; left: 20px; right: 20px; top: 196px;
    height: 1px; background: var(--accent); opacity: 0.25;
  }
  .format {
    position: absolute; left: 20px; top: 210px;
    display: flex; align-items: center; gap: 10px;
  }
  .format__icon {
    width: 38px; height: 38px; border-radius: 50%;
    background: var(--accent);
    display: flex; align-items: center; justify-content: center;
  }
  .format__icon svg { width: 20px; height: 20px; }
  .format__label { font-size: 11px; font-weight: 500; letter-spacing: 1.2px; text-transform: uppercase; }
</style>
</head>
<body>

<article class="post post--training">
  <div class="post__photo" role="img" aria-label="Portret van de trainer"></div>
  <div class="brand"><span class="brand__dot"></span>Bright Path Academy</div>
  <div class="content">
    <h2 class="headline headline--caps">PRE-NEW<br>YEAR’S EVE</h2>
    <p class="detail">Dinsdag 29dec<br>19-21u</p>
  </div>
  <div class="rule"></div>
  <div class="format">
    <span class="format__icon">
      <svg viewBox="0 0 24 24" fill="none" stroke="var(--white)" stroke-width="1.8" stroke-linecap="round" stroke-linejoin="round">
        <rect x="3" y="4" width="18" height="12" rx="2"/><path d="M9 20h6M12 16v4"/><path d="M10 8l4 2-4 2z" fill="var(--white)"/>
      </svg>
    </span>
    <span class="format__label">online training</span>
  </div>
</article>

<article class="post post--blog">
  <div class="post__photo" role="img" aria-label="Notitieblok met voornemens en een pen"></div>
  <div class="brand"><span class="brand__dot"></span>Bright Path Academy</div>
  <div class="content">
    <h2 class="headline">Goede voornemens die je volhoudt</h2>
    <p class="detail">3 tips</p>
  </div>
  <div class="rule"></div>
  <div class="format">
    <span class="format__icon">
      <svg viewBox="0 0 24 24" fill="none" stroke="var(--white)" stroke-width="1.8" stroke-linecap="round" stroke-linejoin="round">
        <path d="M6 3h9l4 4v14H6z"/><path d="M9 11h7M9 14h7M9 17h4"/>
      </svg>
    </span>
    <span class="format__label">blog</span>
  </div>
</article>

<article class="post post--facts">
  <div class="post__photo" role="img" aria-label="Portret van een vrouw bij het raam"></div>
  <div class="brand"><span class="brand__dot"></span>Bright Path Academy</div>
  <div class="content">
    <h2 class="headline">Gemiddeld haalt slechts 20% zijn/haar goede voornemens</h2>
  </div>
  <div class="rule"></div>
  <div class="format">
    <span class="format__icon">
      <svg viewBox="0 0 24 24" fill="none" stroke="var(--white)" stroke-width="1.8" stroke-linecap="round" stroke-linejoin="round">
        <path d="M4 5h16v11h-9l-4 4v-4H4z"/><path d="M12 8v4"/><circle cx="12" cy="14" r="0.6" fill="var(--white)"/>
      </svg>
    </span>
    <span class="format__label">facts</span>
  </div>
</article>

<article class="post post--podcast">
  <div class="post__photo" role="img" aria-label="Portret van de podcastgast"></div>
  <div class="brand"><span class="brand__dot"></span>Bright Path Academy</div>
  <div class="content">
    <p class="kicker">Kijk eens verder met</p>
    <h2 class="headline headline--caps">JORIS<br>VERHOEF</h2>
  </div>
  <div class="rule"></div>
  <div class="format">
    <span class="format__icon">
      <svg viewBox="0 0 24 24" fill="none" stroke="var(--white)" stroke-width="1.8" stroke-linecap="round" stroke-linejoin="round">
        <rect x="9" y="3" width="6" height="11" rx="3"/><path d="M5 11a7 7 0 0 0 14 0M12 18v3"/>
      </svg>
    </span>
    <span class="format__label">podcast</span>
  </div>
</article>

</body>
</html>
```